Velmora Nightclub Flyer (Updated)

Flyer for facebook, square is fine, or rectangular. Here is the text:
VELMORA
Nightclub + Lounge
presents

B2B THURSDAY
Nov 29 2018

CLUB FLOOR:
ROLF B2B GARTH
BENEDICT SALVORTE

LOUNGE:
TOBY B2B MY COUSIN
THUNDER REGGIE

Powered by KELP Acoustics
4726 8th Avenue 21+ 9pm-2am
velmorakestrel.com for VIP booth inquiries

Target Market(s)

Nightclub

Industry/Entity Type

Night Club

Font styles to use
Sans Serif

Colors

Designer to choose colors to be used in the design.

Requirements
Must have
• All the text listed, and plz keep the theme of the attached files. We want to stay consistent with the Velmora brand
Nice to have
• Try to stay with the theme from the attachments
Should not have
• Dont' stray to far from the general theme we have from the attachments

```html
<!DOCTYPE html>
<html lang="en">
<head>
<meta charset="utf-8">
<title>Velmora presents B2B Thursday</title>
<link rel="stylesheet" href="https://fonts.googleapis.com/css2?family=Jost:wght@400&display=swap">
<style>
  :root {
    --paper-light: #f5ecd4;
    --paper-mid: #e6d6b0;
    --paper-edge: #c9b58a;
    --frame: #b89c6e;
    --cream: #f4e8c8;
    --ink: #3a2a22;
    --footer-bg: #f3e8cc;
    --rule: #6a4a3a;
  }
  html, body {
    margin: 0;
    padding: 0;
    overflow: hidden;
    background: #ffffff;
  }
  .flyer {
    position: relative;
    width: 1076px;
    height: 1200px;
    overflow: hidden;
    font-family: "Jost", sans-serif;
    font-weight: 400;
    color: var(--ink);
  }
  .backdrop {
    position: absolute;
    inset: 0;
    background: radial-gradient(ellipse at 50% 45%, var(--paper-light) 0%, var(--paper-mid) 60%, var(--paper-edge) 100%);
  }
  .feature {
    position: absolute;
    left: 0;
    top: 0;
  }
  .brand {
    position: absolute;
    left: 0;
    width: 1076px;
    text-align: center;
    color: var(--cream);
    line-height: 1;
  }
  .brand-name {
    top: 532px;
    font-size: 78px;
    letter-spacing: 4px;
  }
  .brand-sub {
    top: 622px;
    font-size: 25px;
    letter-spacing: 4px;
  }
  .brand-presents {
    top: 692px;
    font-size: 36px;
  }
  .lineup {
    position: absolute;
    top: 960px;
    left: 0;
    width: 1076px;
    height: 90px;
    font-size: 22px;
    line-height: 29.5px;
  }
  .lineup-col {
    position: absolute;
    top: 0;
    text-align: center;
    white-space: nowrap;
    transform: translateX(-50%);
  }
  .col-night { left: 249px; }
  .col-club { left: 491px; }
  .col-lounge { left: 782px; }
  .footer {
    position: absolute;
    left: 0;
    top: 1074px;
    width: 1076px;
    height: 126px;
    background: var(--footer-bg);
  }
  .footer-rule {
    position: absolute;
    left: 0;
    top: 1048px;
  }
  .footer-text {
    position: absolute;
    left: 0;
    width: 1076px;
    text-align: center;
    line-height: 1;
  }
  .footer-power { top: 1094px; font-size: 16.5px; }
  .footer-venue { top: 1122px; font-size: 16.5px; }
  .footer-web { top: 1147px; font-size: 24px; letter-spacing: 0.5px; }
</style>
</head>
<body>
<div class="flyer">
  <div class="backdrop" role="img" aria-label="Soft cream paper background with a faint damask pattern"></div>

  <svg class="feature" width="1076" height="1200" viewBox="0 0 1076 1200">
    <defs>
      <radialGradient id="velvet" cx="50%" cy="50%" r="55%">
        <stop offset="0%" stop-color="#6a2c20"/>
        <stop offset="100%" stop-color="#341410"/>
      </radialGradient>
    </defs>
    <polygon points="538,162 914,538 538,914 162,538" fill="#000" opacity="0.15" transform="translate(0,8)"/>
    <polygon points="538,162 914,538 538,914 162,538" fill="url(#velvet)" stroke="var(--frame)" stroke-width="6" role="img" aria-label="Dark burgundy damask panel framed on the cream paper"/>
    <circle cx="538" cy="432" r="66" fill="var(--cream)"/>
  </svg>

  <div class="brand brand-name">VELMORA</div>
  <div class="brand brand-sub">NIGHTCLUB + LOUNGE</div>
  <div class="brand brand-presents">presents</div>

  <div class="lineup">
    <div class="lineup-col col-night">B2B<br>THURSDAY<br>Nov 29 2018</div>
    <div class="lineup-col col-club">CLUB FLOOR:<br>ROLF B2B GARTH<br>BENEDICT SALVORTE</div>
    <div class="lineup-col col-lounge">LOUNGE:<br>TOBY B2B MY COUSIN<br>THUNDER REGGIE</div>
  </div>

  <div class="footer"></div>
  <svg class="footer-rule" width="1076" height="40" viewBox="0 0 1076 40">
    <line x1="135" y1="24" x2="918" y2="24" stroke="var(--rule)" stroke-width="2"/>
    <line x1="135" y1="28" x2="918" y2="28" stroke="var(--rule)" stroke-width="1"/>
    <circle cx="542" cy="16" r="6" fill="var(--rule)"/>
  </svg>
  <div class="footer-text footer-power">Powered by KELP Acoustics</div>
  <div class="footer-text footer-venue">4726 8th Avenue 21+ 9pm-2am</div>
  <div class="footer-text footer-web">velmorakestrel.com for VIP booth inquiries</div>
</div>
</body>
</html>
```